Quorra Computers Customer Acquisition Flyer

I need a flyer design for Quorra Computers which is aimed at acquiring new customers. They will be distributed in a letterbox drop and as handouts.

The design should communicate our ability to aid both consumer and small business with all their IT needs and wants, that we have all tools and skills to assist them. It would look modern, professional with a design on the bolder side of the scale.

Very little text to go on flyer, its more about letting people know who we are, wand what we do.

We do:
Computer hardware / software installation and troubleshooting
Custom built computers
Internet installations / WiFi set up
Network installation and consultation
Computer IT Security
Cloud Computing experts
Certified Vantrex phone technicians.

not all of that needs to be on flyer, but if is an computer or connected to a computer / network, we can help you.

I have no preference on colours apart from logo which should not be changed.

If anyone require any more information to create a flyer, just ask me, as i am not sure how much information is needed.

Flyer should be in A5 format.

Target Market(s)

consumer and small business (1-50 employees)

Industry/Entity Type

Computer Repair

Requirements
Must have
• Clear easy to read text, graphics that convey us as the professionals we are.
• Logo with tag line, Your local IT specialists
• Contact details:
• Mobile: 0472 918 143
• Email: support@quorracomputers.com.au
• Web: www.quorracomputers.com.au
• Be in A5 format
Nice to have
• contact details like mobile to really stand out along with logo.
Should not have
• Go wild, you should not restrict too much the creative people out there.

```html
<!DOCTYPE html>
<html lang="en">
<head>
<meta charset="utf-8">
<title>Quorra Computers – Your Local IT Specialists</title>
<link href="https://fonts.googleapis.com/css2?family=Montserrat:wght@400;600;800&family=Open+Sans:wght@400;600&display=swap" rel="stylesheet">
<style>
  :root {
    --red: #e3151b;
    --ink: #1b1b1d;
    --charcoal: #2b2c2f;
    --white: #ffffff;
  }
  * { box-sizing: border-box; margin: 0; padding: 0; }
  html, body { width: 900px; height: 1200px; overflow: hidden; background: var(--white); }
  .flyer {
    position: relative;
    width: 900px;
    height: 1200px;
    overflow: hidden;
    background: var(--white);
    font-family: "Open Sans", Arial, sans-serif;
    color: var(--ink);
  }
  .backdrop { position: absolute; inset: 0; width: 900px; height: 1200px; }

  .brand {
    position: absolute;
    left: 52px;
    top: 52px;
    display: flex;
    align-items: center;
    gap: 12px;
    font-family: "Montserrat", Arial, sans-serif;
    font-weight: 800;
    font-size: 36px;
    color: var(--red);
  }
  .brand-dot { width: 14px; height: 14px; border-radius: 50%; background: var(--red); }

  .tagline {
    position: absolute;
    left: 52px;
    top: 150px;
    font-family: "Montserrat", Arial, sans-serif;
    font-size: 54px;
    line-height: 1.08;
    color: var(--ink);
    text-transform: uppercase;
  }
  .tagline-strong { display: block; font-weight: 800; }
  .tagline-light { display: block; font-weight: 600; }

  .services { position: absolute; left: 52px; top: 325px; width: 420px; }
  .services-heading {
    position: relative;
    display: inline-block;
    background: var(--charcoal);
    color: var(--white);
    font-family: "Montserrat", Arial, sans-serif;
    font-weight: 600;
    font-size: 22px;
    letter-spacing: 1px;
    padding: 5px 18px 5px 14px;
    text-transform: uppercase;
  }
  .services-heading::after {
    content: "";
    position: absolute;
    left: 100%;
    bottom: 0;
    width: 110px;
    height: 3px;
    background: var(--red);
  }
  .services-list { list-style: none; margin-top: 14px; }
  .services-list li {
    position: relative;
    padding-left: 20px;
    font-size: 17px;
    line-height: 1.32;
    color: var(--ink);
    margin-bottom: 3px;
  }
  .services-list li::before {
    content: "";
    position: absolute;
    left: 0;
    top: 8px;
    width: 8px;
    height: 8px;
    background: var(--red);
  }

  .contact {
    position: absolute;
    right: 48px;
    bottom: 30px;
    text-align: right;
    color: var(--white);
  }
  .contact-phone {
    display: flex;
    align-items: center;
    justify-content: flex-end;
    gap: 14px;
    font-family: "Montserrat", Arial, sans-serif;
    font-weight: 600;
    font-size: 48px;
    letter-spacing: 1px;
  }
  .contact-lines {
    display: flex;
    gap: 30px;
    justify-content: flex-end;
    margin-top: 14px;
    font-size: 19px;
  }
  .contact-lines span { display: flex; align-items: center; gap: 8px; }
  .icon-badge {
    display: inline-flex;
    align-items: center;
    justify-content: center;
    border-radius: 50%;
    background: var(--red);
  }
</style>
</head>
<body>
<main class="flyer">
  <svg class="backdrop" viewBox="0 0 900 1200" xmlns="http://www.w3.org/2000/svg">
    <defs>
      <linearGradient id="serverTone" x1="0" y1="0" x2="1" y2="1">
        <stop offset="0" stop-color="#3a3d42"/>
        <stop offset="0.5" stop-color="#6d7076"/>
        <stop offset="1" stop-color="#c9cbce"/>
      </linearGradient>
      <linearGradient id="floorTone" x1="0" y1="0" x2="0" y2="1">
        <stop offset="0" stop-color="#f2f3f4"/>
        <stop offset="1" stop-color="#b9bbbf"/>
      </linearGradient>
      <radialGradient id="robotTone" cx="0.5" cy="0.5" r="0.5">
        <stop offset="0" stop-color="#e6e7e9"/>
        <stop offset="0.7" stop-color="#a7a9ad"/>
        <stop offset="1" stop-color="#a7a9ad" stop-opacity="0"/>
      </radialGradient>
    </defs>

    <path d="M0 780 C 200 720 420 660 600 620 L 900 600 L 900 1200 L 0 1200 Z" fill="url(#floorTone)"/>

    <path role="img" aria-label="Photo of a data centre aisle lined with server racks"
          d="M530 0 L900 0 L900 685 C 800 670 710 620 640 500 C 580 370 580 150 530 0 Z"
          fill="url(#serverTone)"/>

    <path d="M470 0 L530 0 C 580 150 580 370 640 500 C 710 620 800 670 900 685 L 900 720 C 790 700 680 640 610 520 C 540 380 540 150 470 0 Z"
          fill="var(--red)"/>
    <path d="M615 525 C 520 630 340 700 180 760 C 100 790 35 830 0 870 L 0 915 C 50 862 125 822 215 792 C 390 732 550 650 645 548 Z"
          fill="var(--red)"/>

    <ellipse role="img" aria-label="Illustration of a chrome robotic hand resting on a computer mouse"
             cx="540" cy="880" rx="300" ry="160" fill="url(#robotTone)"/>

    <path d="M0 1010 C 250 1080 520 990 900 1030 L 900 1200 L 0 1200 Z" fill="var(--red)"/>
    <path d="M0 1040 C 260 1110 520 1020 900 1060 L 900 1200 L 0 1200 Z" fill="var(--charcoal)"/>
  </svg>

  <div class="brand"><span class="brand-dot"></span>Quorra Computers</div>

  <h1 class="tagline">
    <span class="tagline-strong">Your Local</span>
    <span class="tagline-light">IT Specialists</span>
  </h1>

  <section class="services">
    <h2 class="services-heading">What We Do</h2>
    <ul class="services-list">
      <li>Computer hardware / software installation and troubleshooting</li>
      <li>Custom built computers</li>
      <li>Internet installations / WiFi set up</li>
      <li>Network installation and consultation</li>
      <li>Computer IT Security</li>
      <li>Cloud Computing experts</li>
      <li>Certified Vantrex phone technicians.</li>
    </ul>
  </section>

  <footer class="contact">
    <div class="contact-phone">
      <span class="icon-badge" style="width:44px;height:44px;">
        <svg width="24" height="24" viewBox="0 0 24 24" aria-hidden="true"><path fill="#fff" d="M6.6 10.8a15.1 15.1 0 0 0 6.6 6.6l2.2-2.2c.3-.3.7-.4 1-.2 1.1.4 2.3.6 3.6.6.6 0 1 .4 1 1V20c0 .6-.4 1-1 1A17 17 0 0 1 3 4c0-.6.4-1 1-1h3.5c.6 0 1 .4 1 1 0 1.3.2 2.5.6 3.6.1.3 0 .7-.2 1z"/></svg>
      </span>
      0472 918 143
    </div>
    <div class="contact-lines">
      <span>support@quorracomputers.com.au</span>
      <span><span class="icon-badge" style="width:18px;height:18px;"></span>www.quorracomputers.com.au</span>
    </div>
  </footer>
</main>
</body>
</html>
```